PitchTally Webpages and Logo

See attached brief. Take the existing website www.pitchtally.co.uk and logo and transform these assets to:

Give people who arrive on the site for first time the confidence to sign-up easily and quickly
Allow regular returning users quick and easy placing of predictions and encourage them to share the PitchTally prediction on social networks and with their contacts
Convey the essence of a community working together to enjoyably come-up with smart predictions on sporting events
Work seamlessly and well across smartphones, tablets and desktop i.e. Should be Responsive Web Design
Updates

Target Market(s)

Users are sports fans with opinions
Primarily male and early twenties to mid-thirties
They are competitive - they want to beat their peers
Many are from outside the UK

Industry/Entity Type

Events

Logo Text

PitchTally

Coding

Coded - Design and coding required

Number of Pages Required

4 page

Font styles to use
Sans Serif

Requirements
Must have
• Responsive Web Design
• Mobile First
• HTML must work with dedicated bespoke application developed in ASP.NET using MS SQL underneath
• See Brief
Nice to have
• See brief
Should not have
• See brief

```html
<!DOCTYPE html>
<html lang="en">
<head>
<meta charset="utf-8">
<title>PitchTally – Predict scores</title>
<link rel="stylesheet" href="https://fonts.googleapis.com/css2?family=Noto+Serif:wght@400;700&family=Open+Sans:wght@400;600&display=swap">
<style>
:root{
  --navy:#041421;
  --navy-mid:#0a2c45;
  --glow:#2f8fc9;
  --brand:#0a7dbf;
  --brand-dark:#0667a3;
  --green:#1f9a1f;
  --green-dark:#137a13;
  --white:#ffffff;
  --panel:#ffffff;
  --grey-band:#efefef;
  --text:#555a5f;
  --muted:#777c80;
  --heading:#4a4f54;
}
*{margin:0;padding:0;box-sizing:border-box}
html,body{width:746px;height:1200px;overflow:hidden}
body{
  position:relative;
  font-family:"Open Sans",sans-serif;
  color:var(--text);
  background:
    radial-gradient(ellipse 180px 260px at 746px 60px,rgba(210,235,255,.85),rgba(60,150,210,.5) 40%,transparent 75%),
    linear-gradient(100deg,var(--navy) 0%,var(--navy) 55%,var(--navy-mid) 78%,var(--glow) 100%);
}
.abs{position:absolute}
.site-header .brand{left:62px;top:16px;display:flex;align-items:center;gap:8px;color:var(--white);font-family:"Noto Serif",serif;font-weight:700;font-size:24px}
.brand-dot{width:20px;height:20px;border-radius:50%;background:var(--white)}
.account-links{right:72px;top:28px;font-size:8.5px;color:var(--white);letter-spacing:.3px}
.account-links span{margin:0 12px}
.main-nav{left:62px;top:70px;width:623px;height:44px;background:var(--brand);display:flex;align-items:center;padding-left:16px}
.main-nav a{color:var(--white);font-size:8.5px;text-decoration:none;margin-right:30px}
.social{position:absolute;right:14px;top:16px;display:flex;gap:10px}
.social i{width:11px;height:11px;border-radius:50%;background:var(--white);display:block}
.hero{left:62px;top:114px;width:623px;height:248px;overflow:hidden}
.hero-photo{position:absolute;inset:0;background:radial-gradient(ellipse at 55% 75%,#c9c6c2 0%,#7b7a78 30%,transparent 55%),linear-gradient(160deg,#4b5a5e,#3a4a3e 55%,#2c3d30)}
.hero-photo::after{content:"";position:absolute;inset:0;background:rgba(20,25,30,.45)}
.hero h1{position:absolute;top:52px;width:100%;text-align:center;font-family:"Noto Serif",serif;font-size:31px;color:var(--white);font-weight:700}
.hero p{position:absolute;top:100px;left:38px;right:38px;text-align:center;font-size:8.2px;line-height:16px;color:var(--white)}
.join-btn{position:absolute;left:242px;top:152px;width:138px;height:36px;background:linear-gradient(var(--green),var(--green-dark));border-radius:2px;color:var(--white);font-family:"Noto Serif",serif;font-weight:700;font-size:15px;text-align:center;line-height:36px}
.dots{position:absolute;left:293px;top:222px;display:flex;gap:3px}
.dots i{width:7px;height:7px;border-radius:50%;background:var(--white)}
.dots i:first-child{background:var(--brand)}
.how{left:62px;top:362px;width:623px;height:252px;background:var(--panel)}
.section-title{position:absolute;width:100%;text-align:center;font-family:"Noto Serif",serif;font-weight:700;font-size:14.5px;color:var(--heading)}
.how .intro{position:absolute;top:50px;left:14px;right:14px;text-align:center;font-size:8px;line-height:16px;color:var(--muted)}
.step{position:absolute;top:98px;width:140px;text-align:center}
.step-icon{width:60px;height:60px;border-radius:50%;background:var(--brand);margin:0 auto;display:flex;align-items:center;justify-content:center}
.step h3{font-family:"Noto Serif",serif;font-size:10px;color:var(--heading);margin-top:12px}
.step p{font-size:8px;line-height:16px;color:var(--muted);margin-top:6px}
.fixtures{left:62px;top:614px;width:623px;height:288px;background:var(--grey-band)}
.fixture{position:absolute;width:183px;height:113px;background:var(--white)}
.crest{position:absolute;top:18px;width:30px;height:36px;border-radius:4px}
.vs{position:absolute;left:0;right:0;top:34px;text-align:center;font-size:9px;color:var(--text)}
.team{position:absolute;top:63px;font-size:7.5px;color:var(--muted);width:80px;text-align:center}
.predict-btn{position:absolute;left:0;bottom:0;width:100%;height:27px;background:linear-gradient(var(--brand),var(--brand-dark));color:var(--white);font-family:"Noto Serif",serif;font-weight:700;font-size:9px;text-align:center;line-height:27px}
.pundits{left:62px;top:902px;width:623px;height:231px;background:var(--panel)}
.pundit{position:absolute;top:66px;width:220px;text-align:center}
.avatar{width:72px;height:72px;border-radius:50%;margin:0 auto;border:1px solid #cfd3d6;background:radial-gradient(circle at 50% 40%,#d9b79d,#8a6a55 60%,#e7e7e7 62%)}
.pundit h3{font-family:"Noto Serif",serif;font-size:10px;color:var(--brand);margin-top:8px}
.pundit p{font-size:8px;color:var(--muted);margin-top:10px}
.copyright{left:61px;top:1160px;font-size:8px;color:var(--white)}
</style>
</head>
<body>
<header class="site-header">
  <div class="abs brand"><span class="brand-dot"></span>PitchTally</div>
  <div class="abs account-links">LOGIN<span>|</span>REGISTER</div>
</header>

<nav class="abs main-nav">
  <a>Home</a><a>MiniLiga</a><a>Tables</a><a>Kitty</a><a>FAQ</a><a>Me</a>
  <div class="social" aria-label="Social links"><i></i><i></i></div>
</nav>

<section class="abs hero">
  <div class="hero-photo" role="img" aria-label="Blurred photo of footballers contesting the ball on a pitch"></div>
  <h1>Predict 6 scores to win £250,000</h1>
  <p>Predict results, scores and scorers for your free chance to win a £20 Kestrova voucher every week. Overall season winner gets up to £1000 in Kestrova vouchers! No entry fee and no catches.</p>
  <div class="join-btn">Join Now !</div>
  <div class="dots"><i></i><i></i><i></i><i></i></div>
</section>

<section class="abs how">
  <h2 class="section-title" style="top:24px">How To Play</h2>
  <p class="intro">Lorem ipsum dolor sit amet, eum an posse nonumy mediocrem, id vidit aeterno vocibus sit, alia omittam necessitatibus his at. Abhorreant efficiendi cu usu, scripta inermis ex mei, mei cu vero tempor disputationi. No dicat alterum eos, ei eam porro oportere eloquentiam.</p>
  <div class="step" style="left:6px">
    <div class="step-icon"><svg width="20" height="22" viewBox="0 0 20 22"><path d="M5 10V7a5 5 0 0 1 10 0v3" fill="none" stroke="#fff" stroke-width="2.5"/><rect x="2" y="10" width="16" height="11" rx="1" fill="#fff"/><rect x="9" y="13" width="2" height="4" fill="#0a7dbf"/></svg></div>
    <h3>Login</h3><p>Case noluisse cotidieque id pri, ad legere nostro delenit est.</p>
  </div>
  <div class="step" style="left:241px">
    <div class="step-icon"><svg width="20" height="24" viewBox="0 0 20 24"><path d="M1 1h13l5 5v17H1z" fill="#fff"/><rect x="4" y="14" width="2.5" height="6" fill="#0a7dbf"/><rect x="8.5" y="11" width="2.5" height="9" fill="#0a7dbf"/><rect x="13" y="8" width="2.5" height="12" fill="#0a7dbf"/></svg></div>
    <h3>Predict</h3><p>Case noluisse cotidieque id pri, ad legere nostro delenit est.</p>
  </div>
  <div class="step" style="left:477px">
    <div class="step-icon"><svg width="30" height="30" viewBox="0 0 30 30"><circle cx="15" cy="15" r="12.5" fill="none" stroke="#fff" stroke-width="2.5"/><path d="M9 14l4 4 8-8" fill="none" stroke="#fff" stroke-width="2.5"/></svg></div>
    <h3>Enjoy</h3><p>Case noluisse cotidieque id pri, ad legere nostro delenit est.</p>
  </div>
</section>

<section class="abs fixtures">
  <div class="fixture" style="left:18px;top:20px"><span class="crest" style="left:24px;background:#9b8ec4"></span><span class="crest" style="right:24px;background:#d8312a;border-radius:50%"></span><span class="vs">v</span><span class="team" style="left:0">Ashford Vale</span><span class="team" style="right:0">Mercia Town</span><div class="predict-btn">Predict Score Now</div></div>
  <div class="fixture" style="left:220px;top:20px"><span class="crest" style="left:24px;background:#7a2a3e"></span><span class="crest" style="right:24px;background:#1f4f9c;border-radius:50%"></span><span class="vs">v</span><span class="team" style="left:0">Westbrook United</span><span class="team" style="right:0">Lowfield City</span><div class="predict-btn">Predict Score Now</div></div>
  <div class="fixture" style="left:421px;top:20px"><span class="crest" style="left:24px;background:#3c5fa3;border-radius:50%"></span><span class="crest" style="right:24px;background:#1f2f6a"></span><span class="vs">v</span><span class="team" style="left:0">Westbrook United</span><span class="team" style="right:0">Lowfield City</span><div class="predict-btn">Predict Score Now</div></div>
  <div class="fixture" style="left:18px;top:151px"><span class="crest" style="left:24px;background:#1b2353;width:14px;margin-left:8px"></span><span class="crest" style="right:24px;background:#e8d23a"></span><span class="vs">v</span><span class="team" style="left:0">Ashford Vale</span><span class="team" style="right:0">Mercia Town</span><div class="predict-btn">Predict Score Now</div></div>
  <div class="fixture" style="left:220px;top:151px"><span class="crest" style="left:24px;background:#7fb0d8"></span><span class="crest" style="right:24px;background:#2f58a8"></span><span class="vs">v</span><span class="team" style="left:0">Westbrook United</span><span class="team" style="right:0">Lowfield City</span><div class="predict-btn">Predict Score Now</div></div>
  <div class="fixture" style="left:421px;top:151px"><span class="crest" style="left:24px;background:#3c5fa3;border-radius:50%"></span><span class="crest" style="right:24px;background:#1f2f6a"></span><span class="vs">v</span><span class="team" style="left:0">Westbrook United</span><span class="team" style="right:0">Lowfield City</span><div class="predict-btn">Predict Score Now</div></div>
</section>

<section class="abs pundits">
  <h2 class="section-title" style="top:24px">Pundits Predictions</h2>
  <div class="pundit" style="left:46px"><div class="avatar" role="img" aria-label="Portrait photo of pundit Janine Carter"></div><h3>Janine Carter</h3><p>I haven't made my predictions yet, check back later</p></div>
  <div class="pundit" style="left:353px"><div class="avatar" role="img" aria-label="Portrait photo of pundit Geoff Hartley"></div><h3>Geoff Hartley</h3><p>I haven't made my predictions yet, check back later</p></div>
</section>

<footer class="abs copyright">Copyright @ 2014 PitchTally.All Rights Reserved.</footer>
</body>
</html>
```